Business Card Design

Hi I need a business card designed, we already have the business name logo artwork and would like some concept ideas for the Bus Card layout.
On the back of the card i want to include the products and services that we offer.
We are a Plastics Sheeting manufacture based in Perth Australia.

                                       

We need a BC design for a company called Tarvo Plastics based in Perth Australia.

We supply from DIY to Trade & Industrial  Engineering Markets.

We specialise in:

·         Cut to size panels  (all shapes and sizes)

·         Plastics fabrication & Welding

·         Custom Designs

·         Plastic Repairs

·         PVC Pipe Slotting & PVC Pipe Threading

·         Supplier of all types of engineering plastics and profiles.

Including:           Acrylic / Clarvene

                               Polycarbonate / Dorvil

                               Prismatic Light Diffuser

                               Vantrib

                               HDPE / UHMWPE

                               PVC / PVC Foam

                               Nylon

                               HIPS

```html
<!DOCTYPE html>
<html lang="en">
<head>
<meta charset="utf-8">
<title>Tarvo Plastics – Business Card</title>
<link href="https://fonts.googleapis.com/css2?family=Source+Sans+3:wght@400;600;700;800&display=swap" rel="stylesheet">
<style>
  :root {
    --navy: #1d2a5c;
    --orange: #e07a1f;
    --gold: #f2a623;
    --white: #ffffff;
    --paper: #ffffff;
    --backdrop: #e9e7e3;
    --rule: #8a93b8;
  }
  * { box-sizing: border-box; margin: 0; padding: 0; }
  html, body {
    width: 1200px; height: 720px; overflow: hidden;
    background: var(--backdrop);
    font-family: "Source Sans 3", "Myriad Pro", Arial, sans-serif;
  }
  .sheet {
    width: 1200px; height: 720px;
    display: flex; align-items: center; justify-content: center; gap: 36px;
  }
  .card {
    position: relative;
    width: 560px; height: 320px;
    overflow: hidden;
    box-shadow: 0 4px 14px rgba(0,0,0,.18);
  }

  /* Front */
  .card--front { background: var(--paper); }
  .front-shape { position: absolute; inset: 0; }
  .brand-name {
    position: absolute; left: 0; right: 0; top: 34px;
    text-align: center;
    font-weight: 800; font-size: 52px; line-height: 1;
    color: var(--navy); letter-spacing: .5px;
  }
  .person {
    position: absolute; left: 0; right: 0; top: 100px;
    text-align: center; font-weight: 700; font-size: 17px; color: var(--navy);
  }
  .person .title { color: var(--orange); font-weight: 600; }
  .address {
    position: absolute; right: 300px; top: 178px;
    text-align: right; color: var(--white); font-style: normal;
    font-size: 12.5px; line-height: 17px;
  }
  .contact-divider {
    position: absolute; left: 272px; top: 150px; width: 1px; height: 150px;
    background: var(--rule);
  }
  .contacts {
    position: absolute; left: 288px; top: 140px;
    list-style: none; color: var(--white); font-size: 12.5px;
  }
  .contacts li { display: flex; align-items: center; gap: 8px; height: 26px; }
  .contacts svg { width: 13px; height: 13px; fill: var(--white); flex: none; }

  /* Back */
  .card--back { background: var(--navy); color: var(--white); }
  .back-brand {
    position: absolute; left: 0; right: 0; top: 24px;
    text-align: center; font-weight: 800; font-size: 50px; line-height: 1;
    color: var(--white); letter-spacing: .5px;
  }
  .tagline {
    position: absolute; left: 0; right: 0; top: 88px;
    text-align: center; font-weight: 700; font-size: 13.5px; line-height: 17px;
  }
  .offer-col { position: absolute; top: 134px; }
  .offer-col--services { left: 26px; width: 310px; }
  .offer-col--materials { left: 362px; width: 180px; }
  .offer-heading {
    color: var(--gold); font-weight: 700; font-size: 18px; margin-bottom: 4px;
  }
  .offer-list { list-style: none; font-size: 13.5px; line-height: 19px; }
  .offer-list li { position: relative; padding-left: 13px; }
  .offer-list li::before {
    content: ""; position: absolute; left: 0; top: 7px;
    width: 6px; height: 6px; border-radius: 50%; background: var(--gold);
  }
  .offer-list .pair-sep {
    display: inline-block; width: 6px; height: 6px; border-radius: 50%;
    background: var(--gold); margin: 0 5px 2px 7px; vertical-align: middle;
  }
  .column-divider {
    position: absolute; left: 345px; top: 128px; width: 1px; height: 160px;
    background: var(--rule);
  }
</style>
</head>
<body>
<main class="sheet">

  <section class="card card--front" aria-label="Business card front">
    <svg class="front-shape" viewBox="0 0 560 320" preserveAspectRatio="none" aria-hidden="true">
      <path d="M0,212 C170,158 380,128 560,126 L560,320 L0,320 Z" fill="var(--navy)"/>
      <path d="M0,198 C170,143 380,113 560,111" fill="none" stroke="var(--orange)" stroke-width="4"/>
    </svg>

    <h1 class="brand-name">Tarvo Plastics</h1>
    <p class="person">Your Name, <span class="title">Title</span></p>

    <address class="address">
      Unit 4/18 Harlow Circuit<br>
      Bramley Park WA 6028<br>
      PO Box 2270<br>
      Bramley Park DC WA 6941<br>
      Tarvo Holdings Pty Ltd<br>
      T/A Tarvo Plastics ABN: TBA
    </address>

    <div class="contact-divider"></div>

    <ul class="contacts">
      <li>
        <svg viewBox="0 0 16 16" aria-hidden="true"><circle cx="8" cy="8" r="7.5" fill="none" stroke="#fff" stroke-width="1.2"/><path d="M5 4.2l1.6-.4 1 2.2-1 .8a6 6 0 0 0 2.6 2.6l.8-1 2.2 1-.4 1.6c-3.9.2-7-2.9-6.8-6.8z"/></svg>
        08 9000 4117
      </li>
      <li>
        <svg viewBox="0 0 16 16" aria-hidden="true"><path d="M4.5 1h7a1 1 0 0 1 1 1v12a1 1 0 0 1-1 1h-7a1 1 0 0 1-1-1V2a1 1 0 0 1 1-1zm.8 2v8.5h5.4V3zM8 12.3a.9.9 0 1 0 0 1.8.9.9 0 0 0 0-1.8z"/></svg>
        555-010-4420
      </li>
      <li>
        <svg viewBox="0 0 16 16" aria-hidden="true"><path d="M4 1h6l2 2v3H4zM1.5 7h13a1 1 0 0 1 1 1v5h-3v2h-9v-2h-3V8a1 1 0 0 1 1-1zm3.5 5v2h6v-2z"/></svg>
        08 9000 4118
      </li>
      <li>
        <svg viewBox="0 0 16 16" aria-hidden="true"><path d="M1 3h14v10H1zm1.4 1.2L8 8.6l5.6-4.4z"/></svg>
        sales@tarvoplastics.com.au
      </li>
    </ul>
  </section>

  <section class="card card--back" aria-label="Business card back">
    <h2 class="back-brand">Tarvo Plastics</h2>
    <p class="tagline">The Products And Services That We Offer<br>Are Supplied From Diy To Trade &amp; Industrial Engineering Markets</p>

    <div class="offer-col offer-col--services">
      <h3 class="offer-heading">We specialise in:</h3>
      <ul class="offer-list">
        <li>Cut to size panels (all shapes and sizes)</li>
        <li>Plastics fabrication &amp; Welding</li>
        <li>Custom Designs</li>
        <li>Plastic Repairs</li>
        <li>PVC Pipe Slotting &amp; PVC Pipe Threading</li>
        <li>Supplier of all types of engineering<br>plastics and profiles</li>
      </ul>
    </div>

    <div class="column-divider"></div>

    <div class="offer-col offer-col--materials">
      <h3 class="offer-heading">Including:</h3>
      <ul class="offer-list">
        <li>Acrylic / Clarvene</li>
        <li>Polycarbonate / Dorvil</li>
        <li>Prismatic Light Diffuser</li>
        <li>Vantrib<span class="pair-sep"></span>HDPE / UHMWPE</li>
        <li>PVC / PVC Foam</li>
        <li>Nylon<span class="pair-sep"></span>HIPS</li>
      </ul>
    </div>
  </section>

</main>
</body>
</html>
```